Business cards to launch an education platform

Hi,
I am looking at having new business cards designed.
I am a startup, developing a web platform for schools and university, the education world. It's an online assessment system.
I would like a card that looks classy, and that is using the colors and the font of my logo.

I have attached:
1) my logo
2) A business card that I have designed quickly so you can have all the information required in the card, but I really don't like it.
3) The font that I am using (Lato Regular) to design my web platform
4) Some screenshots of my web platform so you can have a look at the style that I have.

Target Market(s)

Major market: Education system: Schools and university
Minor markets: Business in general

Industry/Entity Type

Business

Contact Information for Business Card

Clara Fenwick
Director

M: 0437 518 902
E: clara.fenwick@amberLoomSystems.com.au

Requirements
Must have
• The colors of my logo

```html
<!DOCTYPE html>
<html lang="en">
<head>
<meta charset="utf-8">
<title>Amber Loom Systems – Business Card</title>
<link href="https://fonts.googleapis.com/css2?family=Exo+2:wght@400;500;600&family=Lato:wght@400;700&display=swap" rel="stylesheet">
<style>
  :root {
    --backdrop: #ece8e3;
    --card-white: #ffffff;
    --blue-deep: #0a6bb5;
    --blue-mid: #1787cf;
    --blue-light: #2aa3e0;
    --cyan-line: #38c8f0;
    --brand-blue: #1f6fb0;
    --text-white: #ffffff;
    --shadow: rgba(40, 30, 20, 0.35);
  }
  * { margin: 0; padding: 0; box-sizing: border-box; }
  html, body {
    width: 1200px; height: 753px; overflow: hidden;
    background: var(--backdrop);
  }
  .stage { position: relative; width: 1200px; height: 753px; }
  .card {
    position: absolute; top: 226px;
    width: 505px; height: 286px;
    background: var(--card-white);
    box-shadow: 0 3px 10px var(--shadow);
    overflow: hidden;
  }
  .card--front { left: 74px; }
  .card--back { left: 589px; }

  .front-band { position: absolute; inset: 0; width: 505px; height: 286px; }

  .contact-list {
    position: absolute; left: 30px; top: 36px;
    list-style: none;
    font-family: "Lato", sans-serif; font-size: 11px;
    color: var(--text-white); letter-spacing: 0.3px;
  }
  .contact-list li { display: flex; align-items: center; height: 21px; }
  .contact-list li.address { align-items: flex-start; height: 28px; padding-top: 3px; line-height: 12px; font-size: 9.5px; }
  .contact-icon {
    width: 12px; height: 12px; margin-right: 8px; flex: none;
    background: var(--text-white); border-radius: 2px;
    display: flex; align-items: center; justify-content: center;
  }
  .contact-icon svg { width: 9px; height: 9px; }

  .holder {
    position: absolute; right: 18px; top: 120px; text-align: right;
    font-family: "Exo 2", sans-serif; color: var(--text-white);
  }
  .holder-name { font-size: 19px; font-weight: 500; letter-spacing: 1.5px; text-transform: uppercase; line-height: 1; }
  .holder-title { font-size: 9px; font-weight: 500; letter-spacing: 1px; margin-top: 3px; }

  .brand {
    position: absolute; display: flex; align-items: center;
    font-family: "Exo 2", sans-serif; font-weight: 500;
    color: var(--brand-blue); text-transform: uppercase;
  }
  .brand-square { background: var(--brand-blue); flex: none; }
  .brand--small { left: 0; right: 0; top: 212px; justify-content: center; font-size: 19px; letter-spacing: 1.5px; }
  .brand--small .brand-square { width: 30px; height: 30px; margin-right: 12px; }
  .brand--large { left: 0; right: 0; top: 116px; justify-content: center; font-size: 27px; letter-spacing: 2px; }
  .brand--large .brand-square { width: 52px; height: 52px; margin-right: 16px; }
</style>
</head>
<body>
<main class="stage">
  <section class="card card--front">
    <svg class="front-band" viewBox="0 0 505 286" aria-hidden="true">
      <defs>
        <radialGradient id="bandGlow" cx="0.45" cy="0.3" r="0.7">
          <stop offset="0" stop-color="#2aa3e0"/>
          <stop offset="0.55" stop-color="#1787cf"/>
          <stop offset="1" stop-color="#0a6bb5"/>
        </radialGradient>
      </defs>
      <polygon points="0,0 505,0 505,170 343,170 263,134 183,176 0,176" fill="url(#bandGlow)"/>
      <polyline points="0,180 185,180 263,140 340,174 505,174" fill="none" stroke="#38c8f0" stroke-width="5"/>
    </svg>

    <ul class="contact-list">
      <li><span class="contact-icon"><svg viewBox="0 0 10 10"><path d="M2 1l2 2-1 1c.6 1.3 1.6 2.3 3 3l1-1 2 2-1.5 1.5C4 9 1 6 .5 2.5z" fill="#1787cf"/></svg></span>0437 518 902</li>
      <li><span class="contact-icon"><svg viewBox="0 0 10 10"><rect x="2.5" y="0.5" width="5" height="9" rx="1" fill="#1787cf"/></svg></span>0291 734 560</li>
      <li><span class="contact-icon"><svg viewBox="0 0 10 10"><rect x="1" y="2.5" width="8" height="5.5" fill="#1787cf"/><path d="M1 2.5l4 3 4-3" stroke="#fff" stroke-width="0.8" fill="none"/></svg></span>clara.fenwick@amberLoomSystems.com.au</li>
      <li><span class="contact-icon"><svg viewBox="0 0 10 10"><circle cx="5" cy="5" r="3.8" fill="none" stroke="#1787cf" stroke-width="1.2"/><path d="M1.2 5h7.6M5 1.2v7.6" stroke="#1787cf" stroke-width="0.8"/></svg></span>www.amberloomsystems.com.au</li>
      <li class="address"><span class="contact-icon"><svg viewBox="0 0 10 10"><path d="M5 9.5C3 7 2 5.5 2 4a3 3 0 016 0c0 1.5-1 3-3 5.5z" fill="#1787cf"/></svg></span><span>14 Harbour Lane,<br>Level 3 Building</span></li>
    </ul>

    <div class="holder">
      <p class="holder-name">Clara Fenwick</p>
      <p class="holder-title">GENERAL MANAGER</p>
    </div>

    <div class="brand brand--small"><span class="brand-square"></span>Amber Loom Systems</div>
  </section>

  <section class="card card--back">
    <div class="brand brand--large"><span class="brand-square"></span>Amber Loom Systems</div>
  </section>
</main>
</body>
</html>
```